Webdesign für Hersteller für Pack- und Palettieranlagen für den Getränke- und Lebensmittelbereich
Webdesign für Hersteller für Pack- und Palettieranlagen für den Getränke- und Lebensmittelbere..
Zielgruppe
Hersteller für Pack- und Palettieranlagen für den Getränke- und Lebensmittelbereich
Zielgruppe: Getränke- und Lebensmittelhersteller
Aufgabenstellung
die zukünftige Seite soll dynamischer und intuitiver werden
klare Strukturen, aber morderner als das jetztige Layout
Keine Kopie der alten Seite www.kolmatech.de!
Startseite soll aufgeräumter sein
Logo, Rufnummer, Mail, Social Media
Startseite mit großem Headerbild (Slider)

```html
<!DOCTYPE html>
<html lang="de">
<head>
<meta charset="utf-8">
<title>Kolmatech Maschinenbau</title>
<link href="https://fonts.googleapis.com/css2?family=Roboto:wght@400;500;700;900&display=swap" rel="stylesheet">
<style>
:root{
  --green:#6ab42d;
  --green-dark:#4f8f1c;
  --orange:#f39325;
  --ink:#333333;
  --muted:#666666;
  --grey:#8c8c8c;
  --footer:#4a4a4a;
  --footer-dark:#3b3b3b;
  --white:#ffffff;
}
*{margin:0;padding:0;box-sizing:border-box}
html,body{width:1200px;height:3196px;overflow:hidden;background:var(--white)}
body{position:relative;font-family:"Roboto",sans-serif;color:var(--ink)}
.abs{position:absolute}
.topbar{left:0;top:0;width:1200px;height:50px;background:var(--green);color:var(--white);font-size:13px;font-weight:500}
.topbar .item{position:absolute;top:17px;display:flex;align-items:center;gap:7px}
.social{position:absolute;top:18px;width:14px;height:14px;border-radius:50%;background:var(--white)}
.brand{left:0;width:1200px;top:72px;text-align:center;font-size:32px;font-weight:900;color:var(--green);letter-spacing:1px;display:flex;justify-content:center;align-items:center;gap:8px}
.brand .dot{width:24px;height:24px;border-radius:50%;background:var(--green)}
.nav{top:139px;left:0;width:1200px;font-size:12px;font-weight:500;text-transform:uppercase}
.nav span{position:absolute;top:0;white-space:nowrap}
.nav .active{border-bottom:2px solid var(--green);padding-bottom:5px}
.hero{left:68px;top:177px;width:1063px;height:499px;border-radius:4px;overflow:hidden;background:linear-gradient(100deg,#3d6b2a 0%,#5a8a45 40%,#8fb37c 70%,#4d7a32 100%)}
.hero h1{position:absolute;left:61px;top:192px;font-size:46px;line-height:43px;font-weight:700;color:var(--white)}
.hero p{position:absolute;left:61px;top:288px;width:580px;font-size:11px;line-height:11px;font-weight:500;color:var(--white)}
.btn{position:absolute;display:flex;align-items:center;justify-content:center;gap:10px;border-radius:4px;color:var(--white);font-size:13px;font-weight:700;box-shadow:0 3px 6px rgba(0,0,0,.2)}
.btn-orange{background:var(--orange)}
.btn-green{background:var(--green)}
.dots{position:absolute;left:493px;top:474px;display:flex;gap:12px}
.dots i{width:6px;height:6px;border-radius:50%;background:var(--white)}
.section-title{left:0;width:1200px;text-align:center;font-size:27px;font-weight:700;color:#3a3a3a}
.tile{top:779px;width:156px;height:98px;background:var(--white);box-shadow:0 4px 14px rgba(0,0,0,.1);border-radius:3px;text-align:center;font-size:10px;font-weight:500;color:var(--muted)}
.tile svg{margin-top:18px}
.tile span{display:block;margin-top:10px}
.tile.on{color:var(--green)}
.machine{top:930px;width:236px;height:234px;border-radius:3px;overflow:hidden;box-shadow:0 3px 8px rgba(0,0,0,.2)}
.machine .photo{height:187px;background:linear-gradient(160deg,#9aa3a8,#5e676c)}
.machine .label{height:47px;background:var(--grey);color:var(--white);font-size:14px;font-weight:700;display:flex;align-items:center;justify-content:center}
.machine.on .label{background:var(--green)}
.news-card{top:1260px;width:325px;height:155px;background:var(--white);box-shadow:0 3px 12px rgba(0,0,0,.1);border-radius:3px}
.news-meta{font-size:8px;color:var(--muted)}
.news-title{font-size:12px;font-weight:700}
.news-title.hl{color:var(--orange)}
.news-text{font-size:9px;line-height:9px;color:#444;width:318px}
.rule{height:1px;background:#ddd}
.tabs{top:1676px;font-size:11px;color:#444}
.tabs span{position:absolute;white-space:nowrap}
.tabs .active{color:var(--green);border-bottom:1px solid var(--green);padding-bottom:3px}
.job{width:276px;height:112px;background:var(--white);box-shadow:0 3px 12px rgba(0,0,0,.1);border-radius:3px;font-size:9px;color:#555}
.job .date{position:absolute;left:14px;top:12px;font-size:7px}
.job h3{position:absolute;left:14px;top:27px;font-size:15px;font-weight:700;color:#444}
.job .exp{position:absolute;left:14px;top:61px}
.job .loc{position:absolute;right:14px;top:61px}
.job .tag{position:absolute;top:88px;display:flex;align-items:center;gap:6px}
.job .tag::before{content:"";width:5px;height:5px;border-radius:50%;background:var(--green)}
.job .apply{position:absolute;right:16px;top:86px;font-weight:700;color:var(--green)}
.job.on{background:var(--green);color:var(--white)}
.job.on h3,.job.on .apply{color:var(--white)}
.job.on .tag::before{background:var(--white)}
.fade{left:0;top:1850px;width:1200px;height:60px;background:linear-gradient(rgba(255,255,255,.5),#fff 85%)}
.about-img{left:62px;top:2118px;width:511px;height:244px;background:linear-gradient(120deg,#b9bcbd,#7d8487 60%,#545a5e)}
.about-text{left:620px;top:2118px;width:460px;font-size:11px;line-height:11px;color:#444}
.about-text p{margin-bottom:11px}
.contact-bg{left:0;top:2482px;width:1200px;height:404px;background:linear-gradient(#fff 0%,#d8d8d8 30%,#9a9a9a 70%,#707070 100%)}
.contact{left:62px;top:2419px;width:1069px;height:374px;background:var(--green);border-radius:3px;overflow:hidden;box-shadow:0 4px 14px rgba(0,0,0,.2)}
.contact .person{position:absolute;left:0;top:0;width:520px;height:374px;background:linear-gradient(110deg,#3f4650,#6b737b 60%,#9aa0a4);clip-path:polygon(0 0,130px 0,520px 374px,0 374px)}
.contact h2{position:absolute;left:558px;top:32px;font-size:25px;font-weight:700;color:var(--white)}
.field{position:absolute;border-bottom:1px solid rgba(255,255,255,.9);color:var(--white);font-size:11px;font-weight:500;padding-bottom:4px}
.btn-dark{background:#555;font-size:14px;font-weight:500}
.footer{left:0;top:2886px;width:1200px;height:167px;background:var(--footer);color:var(--white)}
.footer h4{position:absolute;font-size:11px;font-weight:700;top:34px}
.footer a{position:absolute;font-size:9px;color:var(--white);text-decoration:none;white-space:nowrap}
.footer .small{position:absolute;font-size:8px;color:#ddd;white-space:nowrap}
.copy{left:0;top:3009px;width:1200px;height:44px;background:var(--footer-dark);color:var(--white);font-size:10px;font-weight:700;display:flex;align-items:center;justify-content:center}
</style>
</head>
<body>

<header class="abs topbar">
  <div class="item" style="left:693px">
    <svg width="11" height="11" viewBox="0 0 24 24"><path fill="#fff" d="M6.6 10.8c1.4 2.8 3.8 5.1 6.6 6.6l2.2-2.2c.3-.3.7-.4 1-.2 1.1.4 2.3.6 3.6.6.6 0 1 .4 1 1V20c0 .6-.4 1-1 1C10.6 21 3 13.4 3 4c0-.6.4-1 1-1h3.5c.6 0 1 .4 1 1 0 1.3.2 2.5.6 3.6.1.3 0 .7-.2 1z"/></svg>
    030 4471 / 280 - 0
  </div>
  <div class="item" style="left:858px">
    <svg width="13" height="10" viewBox="0 0 26 20"><rect x="1" y="1" width="24" height="18" fill="#fff"/><path d="M1 1l12 10L25 1" stroke="#6ab42d" stroke-width="2" fill="none"/></svg>
    INFO@KOLMATECH.DE
  </div>
  <i class="social" style="left:1034px"></i>
  <i class="social" style="left:1061px"></i>
  <i class="social" style="left:1088px"></i>
  <i class="social" style="left:1116px"></i>
</header>

<div class="abs brand"><span class="dot"></span>KOLMATECH</div>

<nav class="abs nav">
  <span class="active" style="left:129px">Unternehmen</span>
  <span style="left:247px">Jobs / Karriere</span>
  <span style="left:370px">Palettiertechnik</span>
  <span style="left:508px">Packertechnik</span>
  <span style="left:630px">Fördertechnik</span>
  <span style="left:756px">Anlagen</span>
  <span style="left:836px">Gebrauchtmaschinen</span>
  <span style="left:1007px">Aktuelles</span>
</nav>

<section class="abs hero" role="img" aria-label="Abfüllanlage mit grünen Glasflaschen in der Produktion">
  <h1>Getränke- und<br>Lebensmittelproduktionstechnik</h1>
  <p>Lorem Ipsum Dolor Sit Amet, Consectetur Adipiscing Elit, Sed Do Eiusmod Tempor Incididunt Ut Labore Et Dolore Magna Aliqua. Ut Enim Ad Minim Veniam, Quis Nostrud Exercitation Ullamco Laboris Nisi Ut Aliquip Ex Ea Commodo Consequat.</p>
  <div class="btn btn-orange" style="left:61px;top:369px;width:144px;height:37px">Mehr Erfahren</div>
  <div class="dots"><i></i><i></i><i></i><i></i><i></i></div>
</section>

<h2 class="abs section-title" style="top:712px">PRODUKTE</h2>

<div class="abs tile on" style="left:254px">
  <svg width="46" height="32" viewBox="0 0 46 32" fill="none" stroke="#6ab42d" stroke-width="2"><rect x="4" y="3" width="17" height="8"/><rect x="25" y="3" width="17" height="8"/><rect x="4" y="13" width="17" height="8"/><rect x="25" y="13" width="17" height="8"/><path d="M1 24h44M1 30h44M5 24v6M23 24v6M41 24v6"/></svg>
  <span>PALETTIERTECHNIK</span>
</div>
<div class="abs tile" style="left:433px">
  <svg width="34" height="32" viewBox="0 0 34 32" fill="#777"><path d="M17 2l13 6-13 6L4 8z"/><path d="M3 11l13 6v13L3 24z"/><path d="M31 11l-13 6v13l13-6z"/></svg>
  <span>PACKERTECHNIK</span>
</div>
<div class="abs tile" style="left:611px">
  <svg width="42" height="32" viewBox="0 0 42 32" fill="#777"><rect x="2" y="4" width="17" height="16"/><rect x="23" y="4" width="17" height="16"/><rect x="1" y="22" width="40" height="8" rx="4"/><circle cx="8" cy="26" r="2" fill="#fff"/><circle cx="21" cy="26" r="2" fill="#fff"/><circle cx="34" cy="26" r="2" fill="#fff"/></svg>
  <span>FÖRDERTECHNIK</span>
</div>
<div class="abs tile" style="left:789px">
  <svg width="38" height="34" viewBox="0 0 38 34" fill="#777"><circle cx="15" cy="14" r="10"/><circle cx="15" cy="14" r="4" fill="#fff"/><rect x="13" y="1" width="4" height="26"/><rect x="2" y="12" width="26" height="4"/><path d="M24 20h6l4 6v7H22z"/></svg>
  <span>GEBRAUCHTMASCHINEN</span>
</div>

<div class="abs machine on" style="left:68px"><div class="photo" role="img" aria-label="Portalmaschine in einer Produktionshalle"></div><div class="label">PORTALMASCHINEN</div></div>
<div class="abs machine" style="left:344px"><div class="photo" role="img" aria-label="Einsäulenmaschine mit Greifer"></div><div class="label">EINSÄULENMASCHINEN</div></div>
<div class="abs machine" style="left:619px"><div class="photo" role="img" aria-label="Industrieroboter beim Palettieren"></div><div class="label">INDUSTRIEROBOTER</div></div>
<div class="abs machine" style="left:896px"><div class="photo" role="img" aria-label="Neuglasmaschine mit Kästen"></div><div class="label">NEUGLASMASCHINEN</div></div>

<h2 class="abs section-title" style="top:1206px">AKTUELLES</h2>

<div class="abs news-card" style="left:68px"></div>
<div class="abs news-meta" style="left:68px;top:1426px">März 7, 2024</div>
<div class="abs news-title hl" style="left:68px;top:1444px">Just published my first Journal on the website!</div>
<div class="abs rule" style="left:68px;top:1462px;width:320px"></div>
<div class="abs news-text" style="left:68px;top:1470px">Lorem Ipsum Dolor Sit Amet, Consectetur Adipiscing Elit, Sed Do Eiusmod Tempor Incididunt Ut Labore Et Dolore Magna Aliqua. Ut Enim Ad Minim Veniam, Quis Nostrud Exercitation Ullamco Laboris Nisi Ut Aliquip Ex Ea Commodo Consequat. Duis Aute Irure Dolor In Reprehenderit In Voluptate Velit Esse Cillum Dolore Eu Fugiat Nulla Pariatur. Excepteur Sint Occaecat Cupidatat Non Proident, Sunt In Culpa Qui Officia Deserunt Mollit Anim Id Est Laborum.</div>

<div class="abs news-card" style="left:438px"></div>
<div class="abs news-meta" style="left:438px;top:1426px">März 7, 2024</div>
<div class="abs news-title" style="left:438px;top:1444px">Just published my first Journal on the website!</div>
<div class="abs rule" style="left:438px;top:1462px;width:320px"></div>
<div class="abs news-text" style="left:438px;top:1470px">Lorem Ipsum Dolor Sit Amet, Consectetur Adipiscing Elit, Sed Do Eiusmod Tempor Incididunt Ut Labore Et Dolore Magna Aliqua. Ut Enim Ad Minim Veniam, Quis Nostrud Exercitation Ullamco Laboris Nisi Ut Aliquip Ex Ea Commodo Consequat. Duis Aute Irure Dolor In Reprehenderit In Voluptate Velit Esse Cillum Dolore Eu Fugiat Nulla Pariatur. Excepteur Sint Occaecat Cupidatat Non Proident, Sunt In Culpa Qui Officia Deserunt Mollit Anim Id Est Laborum.</div>

<div class="abs news-meta" style="left:807px;top:1259px">März 7, 2024</div>
<div class="abs news-title" style="left:807px;top:1277px">Just published my first Journal on the website!</div>
<div class="abs news-meta" style="left:807px;top:1300px">März 7, 2024</div>
<div class="abs news-title hl" style="left:807px;top:1318px">Just published my first Journal on the website!</div>
<div class="abs news-meta" style="left:807px;top:1341px">März 7, 2024</div>
<div class="abs news-title" style="left:807px;top:1359px">Just published my first Journal on the website!</div>
<div class="abs news-meta" style="left:807px;top:1382px">März 7, 2024</div>
<div class="abs news-title" style="left:807px;top:1400px">Just published my first Journal on the website!</div>
<div class="abs news-meta" style="left:807px;top:1423px">März 7, 2024</div>
<div class="abs news-title" style="left:807px;top:1441px">Just published my first Journal on the website!</div>
<div class="btn btn-green" style="left:807px;top:1488px;width:143px;height:37px">Alle Nachrichten</div>

<h2 class="abs section-title" style="top:1585px">JOBS / KARRIERE</h2>

<div class="abs tabs" style="left:0;width:1200px">
  <span class="active" style="left:428px">Alle Jobs</span>
  <span style="left:511px">Development</span>
  <span style="left:621px">Marketing</span>
  <span style="left:717px">Specialist</span>
</div>

<div class="abs job" style="left:151px;top:1731px"><span class="date">März 7, 2024</span><h3>SPS-Programmierung</h3><span class="exp">1 bis 6 jahre</span><span class="loc">Lindenau, Germany</span><span class="tag" style="left:14px">5 tage</span><span class="tag" style="left:71px">Praktikant</span><span class="apply">APPLY</span></div>
<div class="abs job on" style="left:458px;top:1731px"><span class="date">März 7, 2024</span><h3>SPS-Programmierung</h3><span class="exp">1 bis 6 jahre</span><span class="loc">Lindenau, Germany</span><span class="tag" style="left:14px">5 tage</span><span class="tag" style="left:71px">Praktikant</span><span class="apply">APPLY</span></div>
<div class="abs job" style="left:766px;top:1731px"><span class="date">März 7, 2024</span><h3>SPS-Programmierung</h3><span class="exp">1 bis 6 jahre</span><span class="loc">Lindenau, Germany</span><span class="tag" style="left:14px">5 tage</span><span class="tag" style="left:71px">Praktikant</span><span class="apply">APPLY</span></div>
<div class="abs job" style="left:151px;top:1864px"><span class="date">März 7, 2024</span><h3>SPS-Programmierung</h3></div>
<div class="abs job" style="left:458px;top:1864px"><span class="date">März 7, 2024</span><h3>SPS-Programmierung</h3></div>
<div class="abs job" style="left:766px;top:1864px"><span class="date">März 7, 2024</span><h3>SPS-Programmierung</h3></div>
<div class="abs fade" style="top:1858px;height:62px"></div>
<div class="abs" style="left:0;top:1920px;width:1200px;height:90px;background:#fff"></div>

<h2 class="abs section-title" style="top:2029px">UNTERNEHMEN</h2>

<div class="abs about-img" role="img" aria-label="Team in Arbeitskleidung begrüßt einen Kunden in der Werkshalle"></div>
<div class="abs about-text">
  <p>Das Traditionsreiche Familienunternehmen Kolmatech, Entwickelt Und Baut Pack- Und Palettieranlagen Für Den Getränke- Und Lebensmittelbereich. Mit Erfahrung Und Know-How Planen Und Konstruieren Wir Moderne Und Effiziente Anlagen, Die Optimal Auf Die Bedürfnisse Unserer Kunden Abgestimmt Sind.</p>
  <p>Wir Bieten Ihnen Individuelle Maschinen Und Anlagen Zur Abfüllung Und Verpackung, Sortier- Und Umpackanlagen Sowie Einen Umfassenden Rundum-Service An. Mit Unseren Weitläufigen Produktionsstätten Sind Wir In Der Lage, Die Vorarbeiten Der Montage Unter Unserem Dach Zu Erledigen, Sodass Der Zeitaufwand Für Den Aufbau Bei Ihnen Vor Ort Gering Ist.</p>
  <p>Die Wartung Der Anlagen Und Ein Ersatzteil-Service Sowie Professionelle Unterstützung Und Hilfestellung Bei Problemen Sind Für Uns Selbstverständliche Dienstleistungen.</p>
</div>
<div class="btn btn-orange" style="left:620px;top:2302px;width:144px;height:37px">Mehr Erfahren</div>

<div class="abs contact-bg" role="img" aria-label="Förderband in einer Fertigungshalle, graustufig"></div>
<section class="abs contact">
  <div class="person" role="img" aria-label="Geschäftsmann im Anzug mit Smartphone in der Hand"></div>
  <h2>KONTAKT</h2>
  <div class="field" style="left:558px;top:113px;width:170px">Vorname</div>
  <div class="field" style="left:767px;top:113px;width:170px">Nachname</div>
  <div class="field" style="left:558px;top:161px;width:170px">Email</div>
  <div class="field" style="left:767px;top:161px;width:170px">Telefonnummer</div>
  <div class="field" style="left:558px;top:218px;width:379px">Schreibe deine Nachricht...</div>
  <div class="btn btn-dark" style="left:558px;top:291px;width:143px;height:37px">
    <svg width="16" height="16" viewBox="0 0 24 24"><path fill="#fff" d="M2 11l20-9-9 20-2-8z"/></svg>Senden
  </div>
</section>

<footer class="abs footer">
  <h4 style="left:52px">QUICKLINKS</h4>
  <a style="left:52px;top:59px">Unternehmen</a><a style="left:144px;top:59px">Packertechnik</a><a style="left:228px;top:59px">Gebrauchtmaschinen</a>
  <a style="left:52px;top:79px">Jobs / Karriere</a><a style="left:144px;top:79px">Fördertechnik</a><a style="left:228px;top:79px">Aktuelles</a>
  <a style="left:52px;top:99px">Palettiertechnik</a><a style="left:144px;top:99px">Anlagen</a>
  <h4 style="left:361px">PRODUKTE</h4>
  <a style="left:361px;top:59px">PALETTIERTECHNIK</a><a style="left:473px;top:59px">FÖRDERTECHNIK</a>
  <a style="left:361px;top:79px">PACKERTECHNIK</a><a style="left:473px;top:79px">GEBRAUCHTMASCHINEN</a>
  <h4 style="left:625px">KONTAKT</h4>
  <a style="left:625px;top:56px;line-height:11px">KOLMATECH Maschinenbau GmbH<br>Am Werkhof 12<br>01234 Lindenau</a>
  <a style="left:790px;top:59px">030 4471 / 280 - 0</a>
  <a style="left:790px;top:79px">030 4471 / 280 - 14</a>
  <a style="left:790px;top:99px">info@kolmatech.de</a>
  <span class="small" style="left:952px;top:40px">Abonnieren Sie den Newsletter</span>
  <div class="abs" style="left:952px;top:55px;width:124px;height:25px;background:#fff;border-radius:2px 0 0 2px;font-size:8px;color:#555;padding:8px 0 0 9px">Email</div>
  <div class="abs" style="left:1076px;top:55px;width:31px;height:25px;background:var(--green);border-radius:0 2px 2px 0;display:flex;align-items:center;justify-content:center">
    <svg width="10" height="10" viewBox="0 0 10 10"><path d="M1 5h7M5 2l3 3-3 3" stroke="#fff" stroke-width="1.6" fill="none"/></svg>
  </div>
</footer>
<div class="abs copy">©2024. Studio Nordlicht All rights reserved</div>

</body>
</html>
```